Design my site www.brieflyledger.com

So here is what I am thinking in terms of design:

https://plenvo.com

https://www.skyluxair.com

http://kalvex.com/harbor-plaza-tower/

I want the theme to be white and blue (royal blue). I attached a paint picture of what I would like the site to look like in terms of placing the text. Generally, what I like about the sites above is that they are simple, you can navigate easily and have some kind of idea of what's going on by looking at the center (picture and motto). Let's establish a clear understanding of how the functional part of the site would look like. Please see the picture attached.

I want to keep it simple: On top would be the Name 'BRIEFLY ledger", somewhere to the right on top on the page would be 'Sign in" button.

In the center would be a picture (maybe a video) with the Motto (on top of it all in capital) OBSERVE NAVIGATE DECIDE and below would be the "sign up now"

Below the picture (like on kalvex.com site) or to the left on top of the page would be "About Us', "Press" "Contact Us' buttons.

Then once the user gets to his page his got 3 tabs " Press Headlines", "Events", " Briefings".

we would keep the same format I only have on the site, but separate for every Tab.

I do not want the user to get distracted. I also want him to be able to access the page though mobile phone and be able to get automatic updates just like Zorvan Pings without having to sign in daily.

The landing page must be minimalist yet with business/corporate feel where users can navigate easily and a "what you see is what you get" approach. You want an image or video (personally I prefer the video.. it does capture the users attention instantly, as long as it is an interesting video), with your taglines in it.

Sections available to public: About Us, Contact Us, Landing Page with Signup Option

Private: Public Sections + User Account Page, Tabs for (Events, Press Headlines, Briefings)

Target Market(s)

PR/media monitoring/diplomatic community

Coding

Coded - Design and coding required

Number of Pages Required

1 page

Font styles to use
Serif
Sans Serif

Colors
0255a3
ec1f27

Requirements
Must have
• a simple landing page, that is user friendly.
Nice to have
• a video with the explanation of how to navigate the site
Should not have
• too many colors, graphs etc.

```html
<!DOCTYPE html>
<html lang="en">
<head>
<meta charset="UTF-8">
<title>Briefly Ledger — Member Tabs</title>
<link rel="stylesheet" href="https://fonts.googleapis.com/css2?family=Michroma&family=Open+Sans:wght@400;600&display=swap">
<style>
  :root {
    --royal-blue: #0255a3;
    --alert-red: #ec1f27;
    --bullet-navy: #1d3a78;
    --ink: #111111;
    --muted: #7a7a7a;
    --meta-ink: #333333;
    --page: #ffffff;
    --photo-blue: #3a4f8f;
    --photo-warm: #b08a62;
    --calendar-grey: #d9d9d9;
  }
  * { box-sizing: border-box; margin: 0; padding: 0; }
  html, body { width: 1200px; height: 600px; overflow: hidden; background: var(--page); }
  body { font-family: "Open Sans", Arial, sans-serif; color: var(--ink); position: relative; }

  .tabs { position: absolute; top: 98px; left: 161px; display: grid; grid-template-columns: repeat(3, 278px); column-gap: 22px; }
  .tab-title {
    height: 66px; background: var(--royal-blue); color: #fff;
    display: flex; align-items: center; justify-content: center;
    font-family: "Michroma", Arial, sans-serif; font-weight: 400; font-size: 12.5px; letter-spacing: 0.3px;
    text-transform: uppercase;
  }

  .item-title { font-size: 12.8px; line-height: 16px; font-weight: 400; color: var(--ink); white-space: nowrap; }
  .item-text { font-size: 11px; line-height: 17.5px; color: var(--muted); margin-top: 3px; white-space: nowrap; }
  .item-meta { font-size: 11.5px; line-height: 16px; margin-top: 4px; margin-left: 2px; color: var(--ink); white-space: nowrap; }
  .item-meta .time { margin-left: 8px; font-size: 12.5px; }
  .item-meta .venue { margin-left: 4px; font-size: 10.5px; color: var(--meta-ink); }

  .headline-list { margin-top: 23px; }
  .headline { display: flex; height: 72px; margin-bottom: 26px; }
  .headline-photo { width: 82px; height: 72px; flex: none; }
  .headline-body { margin-left: 18px; margin-top: 0; }

  .event-photo { display: block; margin-top: 23px; width: 278px; height: 118px; }
  .event-body { margin-top: 24px; }
  .event-body .item-meta .time { margin-left: 20px; }
  .events-button {
    display: inline-flex; align-items: center; justify-content: center;
    margin-top: 17px; width: 134px; height: 39px; background: var(--alert-red);
    color: #fff; font-size: 13.5px; text-transform: uppercase; text-decoration: none;
  }

  .briefing-column { position: relative; }
  .briefing-list { list-style: none; margin-top: 23px; }
  .briefing-list li {
    position: relative; padding-left: 17px; font-size: 11px; line-height: 17.5px;
    color: var(--muted); margin-bottom: 3.5px; white-space: nowrap;
  }
  .briefing-list li::before {
    content: ""; position: absolute; left: 0; top: 6px; width: 5px; height: 5px; background: var(--bullet-navy);
  }
  .read-more {
    position: absolute; right: 9px; top: 342px; font-size: 10.5px; line-height: 14px; color: var(--alert-red);
    text-decoration: none; border-bottom: 1.5px solid var(--alert-red); padding: 0 4px 1px;
  }
</style>
</head>
<body>
  <main class="tabs">
    <section class="headlines-column">
      <h2 class="tab-title">Newspapers Headlines</h2>
      <div class="headline-list">
        <article class="headline">
          <svg class="headline-photo" role="img" aria-label="News anchor at a studio desk" viewBox="0 0 82 72"><defs><linearGradient id="g1" x1="0" y1="0" x2="0" y2="1"><stop offset="0" stop-color="#8a5a4a"/><stop offset="1" stop-color="#3a4f8f"/></linearGradient></defs><rect width="82" height="72" fill="url(#g1)"/></svg>
          <div class="headline-body">
            <h3 class="item-title">Lorem ipsum dolor sit amet,</h3>
            <p class="item-text">Duis autem vel eum iriure dolor in<br>hendrerit invulputate velit.</p>
            <p class="item-meta">Jan 05, 2016 <span class="time">Time</span> <span class="venue">Venue</span></p>
          </div>
        </article>
        <article class="headline">
          <svg class="headline-photo" role="img" aria-label="Portrait of a smiling young man outdoors" viewBox="0 0 82 72"><defs><linearGradient id="g2" x1="0" y1="0" x2="0" y2="1"><stop offset="0" stop-color="#c9b8a0"/><stop offset="1" stop-color="#b08a62"/></linearGradient></defs><rect width="82" height="72" fill="url(#g2)"/></svg>
          <div class="headline-body">
            <h3 class="item-title">Lorem ipsum dolor sit amet,</h3>
            <p class="item-text">Duis autem vel eum iriure dolor in<br>hendrerit invulputate velit.</p>
            <p class="item-meta">Jan 05, 2016 <span class="time">Time</span> <span class="venue">Venue</span></p>
          </div>
        </article>
        <article class="headline">
          <svg class="headline-photo" role="img" aria-label="Portrait of a news presenter in a studio" viewBox="0 0 82 72"><defs><linearGradient id="g3" x1="0" y1="0" x2="1" y2="1"><stop offset="0" stop-color="#2a3a9a"/><stop offset="1" stop-color="#d98a6a"/></linearGradient></defs><rect width="82" height="72" fill="url(#g3)"/></svg>
          <div class="headline-body">
            <h3 class="item-title">Lorem ipsum dolor sit amet,</h3>
            <p class="item-text">Duis autem vel eum iriure dolor in<br>hendrerit invulputate velit.</p>
            <p class="item-meta">Jan 05, 2016 <span class="time">Time</span> <span class="venue">Venue</span></p>
          </div>
        </article>
      </div>
    </section>

    <section class="events-column">
      <h2 class="tab-title">Events</h2>
      <svg class="event-photo" role="img" aria-label="Close-up of calendar pages with dates" viewBox="0 0 278 118"><defs><linearGradient id="g4" x1="0" y1="0" x2="1" y2="0"><stop offset="0" stop-color="#eeeeee"/><stop offset="1" stop-color="#d9d9d9"/></linearGradient></defs><rect width="278" height="118" fill="url(#g4)"/></svg>
      <div class="event-body">
        <h3 class="item-title">Lorem ipsum dolor sit amet,</h3>
        <p class="item-text">Duis autem vel eum iriure dolor in hendrerit invulp<br>utate velit.</p>
        <p class="item-meta">Jan 05, 2014 <span class="time">Time</span> <span class="venue">Venue</span></p>
      </div>
      <a class="events-button" href="#">Our Events</a>
    </section>

    <section class="briefing-column">
      <h2 class="tab-title">Daily Briefing</h2>
      <ul class="briefing-list">
        <li>Duis autem vel eum iriure dolor in hendrerit invulp<br>utate velit.</li>
        <li>Duis autem vel eum iriure dolor in hendrerit invulp<br>utate velit.</li>
        <li>Duis autem vel eum iriure dolor in hendrerit invulp<br>utate velit.</li>
        <li>Duis autem vel eum iriure dolor in hendrerit invulp<br>utate velit.</li>
        <li>Duis autem vel eum iriure dolor in hendrerit invulp<br>utate velit.</li>
        <li>Duis autem vel eum iriure dolor in hendrerit invulp<br>utate velit.</li>
        <li>Duis autem vel eum iriure dolor in hendrerit invulp<br>utate velit.</li>
      </ul>
      <a class="read-more" href="#">Read More</a>
    </section>
  </main>
</body>
</html>
```